Website Design for Architecture Practice

I need a home page and one sidebar/content page for an Architecture practice delivered in PSD.

This archictecture practice specialises in one-off, high end homes and commercial properties (restaurant) heavily influenced by Edmund Harcourt Vale, particularly his work on the Pellworth Museum

I am looking for a home page, and a generic content page where we can outline our services, and showcase our homes.

http://journals.kestrelhill.edu.au/artnotes/Pellworth%20Quayside%202.jpg

Target Market(s)

30-70yr old (typically wealthy) property buyers, developers and investors

Industry/Entity Type

Architecture

Number of Pages Required

2 page

Font styles to use
Serif
Sans Serif

Requirements
Must have
• Home page design
• a Content Page design (ie, top nav with sidebar)
Nice to have
• Use any Edmund Harcourt Vale images you can find via google etc as placeholders for our own photography (ie they don't need to be licensed as we will be replacing with our own commissioned photography). Full color preferred but feel free to experiment with treating any images as you see fit.

```html
<!DOCTYPE html>
<html lang="en">
<head>
<meta charset="utf-8">
<title>Stonereach Architect</title>
<link href="https://fonts.googleapis.com/css2?family=Open+Sans:ital,wght@0,300;0,400;0,600;0,700;1,400;1,600;1,700&display=swap" rel="stylesheet">
<style>
:root{
  --teal:#3fc1cf;
  --teal-dark:#2fa9b6;
  --charcoal:#2b2b2b;
  --charcoal-2:#222;
  --ink:#444;
  --muted:#8a8a8a;
  --paper:#ffffff;
  --mist:#f1f1f1;
  --icon-bg:#4a4a4a;
}
*{box-sizing:border-box;margin:0;padding:0}
html,body{width:736px;height:1200px;overflow:hidden;background:var(--paper)}
body{font-family:"Open Sans",Arial,sans-serif;color:var(--ink);position:relative}

.site-header{height:44px;background:var(--charcoal);display:flex;align-items:center;justify-content:space-between;padding:0 40px 0 32px}
.brand{font-weight:700;font-size:17px;color:var(--paper);letter-spacing:.2px;white-space:nowrap}
.main-nav{display:flex;gap:28px}
.main-nav a{color:#cfcfcf;font-size:11px;text-decoration:none}
.main-nav a.is-active{color:var(--paper);font-weight:600}

.hero{position:relative;height:324px;background:linear-gradient(180deg,#a9c4da 0%,#d7dfe3 30%,#9a8b78 52%,#6d7d64 68%,#3f5864 82%,#2f4650 100%)}
.hero-tagline{position:absolute;left:0;right:0;top:222px;text-align:center;color:var(--paper);font-style:italic;font-weight:600;font-size:15px;line-height:21px;text-shadow:0 1px 3px rgba(0,0,0,.6)}

.services{height:220px;display:flex;justify-content:center;gap:76px;padding-top:30px}
.service{width:170px;text-align:center}
.service-badge{width:116px;height:116px;margin:0 auto;border-radius:50%;border:5px solid var(--teal);background:var(--icon-bg);display:flex;align-items:center;justify-content:center}
.service-name{margin-top:22px;font-size:15px;color:var(--ink);white-space:nowrap}

.welcome{height:202px;background:var(--mist);text-align:center;padding-top:28px}
.welcome h1{font-weight:300;font-size:27px;color:#555;white-space:nowrap}
.welcome h1 strong{font-weight:600;font-style:italic}
.welcome p{width:560px;margin:14px auto 0;font-size:8.5px;line-height:14px;color:var(--muted)}
.read-more{display:inline-block;margin-top:18px;background:#d8d8d8;border:1px solid #c8c8c8;color:#555;font-size:8px;padding:4px 14px}

.showcase{height:190px;background:var(--teal);display:flex;padding:32px 0 0 80px;color:var(--paper)}
.section-title{font-size:21px;font-weight:300;font-style:italic}
.section-title strong{font-weight:700}
.facilities{width:208px}
.facility-list{list-style:none;margin-top:14px}
.facility-list li{display:flex;align-items:center;gap:8px;font-size:8px;line-height:18px;white-space:nowrap}
.gallery{width:374px}
.gallery-head{display:flex;justify-content:space-between;align-items:baseline}
.view-all{color:var(--paper);font-size:9px;font-weight:600;text-decoration:underline}
.gallery-grid{margin-top:12px;background:var(--paper);padding:6px;display:grid;grid-template-columns:repeat(4,1fr);gap:5px}
.thumb{height:46px}

.site-footer{height:190px;background:var(--charcoal);display:flex;padding:24px 0 0 80px;color:#bbb;font-size:8px}
.footer-col h3{font-size:9px;font-weight:400;color:#ddd;letter-spacing:.6px;margin-bottom:10px;white-space:nowrap}
.footer-col h3 strong{font-weight:700;color:var(--paper)}
.col-links{width:112px}
.col-links a{display:block;color:#bbb;text-decoration:none;line-height:15px}
.col-contact{width:176px}
.contact-row{display:flex;gap:8px;margin-bottom:12px;line-height:11px}
.col-news{width:170px}
.col-news p{line-height:11px;margin-bottom:8px}
.field{height:14px;background:var(--paper);color:#999;padding:2px 5px;width:136px;margin-bottom:5px;font-size:7px}
.subscribe{display:inline-block;background:var(--teal);color:var(--paper);padding:2px 9px;font-size:7px}
.social-row{display:flex;align-items:center;gap:8px;margin-bottom:9px;letter-spacing:.6px}
.social-dot{width:19px;height:19px;border-radius:50%;background:var(--paper)}

.legal-bar{height:30px;background:var(--charcoal-2);display:flex;align-items:center;justify-content:space-between;padding:0 80px;font-size:7.5px;color:#999}
</style>
</head>
<body>

<header class="site-header">
  <div class="brand">Stonereach Architect</div>
  <nav class="main-nav">
    <a class="is-active" href="#">Home</a><a href="#">About</a><a href="#">Services</a><a href="#">Gallery</a><a href="#">Contact</a>
  </nav>
</header>

<section class="hero" role="img" aria-label="Photograph of a cantilevered modern house on rocks above a river, surrounded by trees">
  <p class="hero-tagline">We Are An Architecture Business / Practice That Specialises In One-off,<br>High End Homes And Commercial Properties</p>
</section>

<section class="services">
  <div class="service">
    <div class="service-badge">
      <svg width="52" height="52" viewBox="0 0 52 52" aria-hidden="true">
        <g fill="var(--teal)" transform="translate(26 26)">
          <rect x="-5" y="-24" width="10" height="12" rx="1"/>
          <rect x="-5" y="-24" width="10" height="12" rx="1" transform="rotate(45)"/>
          <rect x="-5" y="-24" width="10" height="12" rx="1" transform="rotate(90)"/>
          <rect x="-5" y="-24" width="10" height="12" rx="1" transform="rotate(135)"/>
          <rect x="-5" y="-24" width="10" height="12" rx="1" transform="rotate(180)"/>
          <rect x="-5" y="-24" width="10" height="12" rx="1" transform="rotate(225)"/>
          <rect x="-5" y="-24" width="10" height="12" rx="1" transform="rotate(270)"/>
          <rect x="-5" y="-24" width="10" height="12" rx="1" transform="rotate(315)"/>
          <circle r="16"/>
        </g>
        <circle cx="26" cy="26" r="7" fill="var(--icon-bg)"/>
      </svg>
    </div>
    <div class="service-name">One-off</div>
  </div>
  <div class="service">
    <div class="service-badge">
      <svg width="56" height="46" viewBox="0 0 56 46" aria-hidden="true" fill="none" stroke="#fff" stroke-width="2.5">
        <path d="M6 16 L28 4 L50 16"/>
        <rect x="10" y="16" width="36" height="26"/>
        <rect x="16" y="22" width="6" height="6"/><rect x="25" y="22" width="6" height="6"/><rect x="34" y="22" width="6" height="6"/>
        <rect x="24" y="32" width="8" height="10"/>
      </svg>
    </div>
    <div class="service-name">High End Homes</div>
  </div>
  <div class="service">
    <div class="service-badge">
      <svg width="40" height="60" viewBox="0 0 40 60" aria-hidden="true" fill="#d6d6d6">
        <rect x="19" y="2" width="2" height="8"/>
        <path d="M14 12 L20 8 L26 12 V58 H14 Z"/>
        <rect x="6" y="24" width="8" height="34" fill="#b8b8b8"/>
        <rect x="26" y="20" width="8" height="38" fill="#b8b8b8"/>
      </svg>
    </div>
    <div class="service-name">Commercial Properties</div>
  </div>
</section>

<section class="welcome">
  <h1>Welcome to <strong>Stonereach Architect</strong></h1>
  <p>Each project begins with a quiet study of the site, its light, its slope and the way people will move through it. We shape homes that sit lightly in the landscape, using warm stone, long cantilevers and honest timber. Our studio works closely with every client from first sketch to final handover, keeping the vision clear at every stage. From private riverside retreats to intimate restaurants, we design spaces that feel calm, generous and built to last for generations.</p>
  <span class="read-more">Read More</span>
</section>

<section class="showcase">
  <div class="facilities">
    <h2 class="section-title"><strong>Our</strong> Facilities</h2>
    <ul class="facility-list">
      <li><svg width="8" height="8" viewBox="0 0 8 8"><path d="M1 4 L3 6 L7 1" stroke="#fff" stroke-width="1.4" fill="none"/></svg>Bespoke design for private residences</li>
      <li><svg width="8" height="8" viewBox="0 0 8 8"><path d="M1 4 L3 6 L7 1" stroke="#fff" stroke-width="1.4" fill="none"/></svg>Site studies and planning guidance</li>
      <li><svg width="8" height="8" viewBox="0 0 8 8"><path d="M1 4 L3 6 L7 1" stroke="#fff" stroke-width="1.4" fill="none"/></svg>Interior and landscape planning</li>
      <li><svg width="8" height="8" viewBox="0 0 8 8"><path d="M1 4 L3 6 L7 1" stroke="#fff" stroke-width="1.4" fill="none"/></svg>Restaurant and hospitality fit-outs</li>
      <li><svg width="8" height="8" viewBox="0 0 8 8"><path d="M1 4 L3 6 L7 1" stroke="#fff" stroke-width="1.4" fill="none"/></svg>Project management on site</li>
      <li><svg width="8" height="8" viewBox="0 0 8 8"><path d="M1 4 L3 6 L7 1" stroke="#fff" stroke-width="1.4" fill="none"/></svg>Sustainable materials advice</li>
    </ul>
  </div>
  <div class="gallery">
    <div class="gallery-head">
      <h2 class="section-title"><strong>Our</strong> Gallery</h2>
      <a class="view-all" href="#">View All</a>
    </div>
    <div class="gallery-grid">
      <div class="thumb" role="img" aria-label="Modern house among trees" style="background:linear-gradient(160deg,#7b8f5a,#c9b48a)"></div>
      <div class="thumb" role="img" aria-label="Stone house with terrace" style="background:linear-gradient(160deg,#3a4a3c,#a68b62)"></div>
      <div class="thumb" role="img" aria-label="Curved museum facade by the water" style="background:linear-gradient(160deg,#9fb7cc,#b9b2a6)"></div>
      <div class="thumb" role="img" aria-label="Lit house at dusk" style="background:linear-gradient(160deg,#2d3b56,#c98a4f)"></div>
      <div class="thumb" role="img" aria-label="Low house on a lawn" style="background:linear-gradient(160deg,#9fc1de,#6c8a4a)"></div>
      <div class="thumb" role="img" aria-label="Interior living room" style="background:linear-gradient(160deg,#8c6a4b,#d7c2a2)"></div>
      <div class="thumb" role="img" aria-label="House at night" style="background:linear-gradient(160deg,#1f2a3a,#b4743e)"></div>
      <div class="thumb" role="img" aria-label="House with red roof beside a pool" style="background:linear-gradient(160deg,#a7c7e0,#a3523c)"></div>
    </div>
  </div>
</section>

<footer class="site-footer">
  <div class="footer-col col-links">
    <h3><strong>QUICK</strong> LINKS</h3>
    <a href="#">Home</a><a href="#">About</a><a href="#">Services</a><a href="#">Gallery</a><a href="#">Contact</a>
  </div>
  <div class="footer-col col-contact">
    <h3><strong>CONTACT</strong> ADDRESS</h3>
    <div class="contact-row"><svg width="9" height="11" viewBox="0 0 9 11"><path d="M4.5 0 A4.5 4.5 0 0 1 9 4.5 C9 7 4.5 11 4.5 11 C4.5 11 0 7 0 4.5 A4.5 4.5 0 0 1 4.5 0Z" fill="#ddd"/><circle cx="4.5" cy="4.5" r="1.6" fill="#2b2b2b"/></svg><span>14 Quarry Lane, Riverside<br>Marlow Heights, MH4 2QL</span></div>
    <div class="contact-row"><svg width="9" height="9" viewBox="0 0 9 9"><path d="M1 0 H3 L4 2.5 L2.7 3.5 A6 6 0 0 0 5.5 6.3 L6.5 5 L9 6 V8 A1 1 0 0 1 8 9 A8 8 0 0 1 0 1 A1 1 0 0 1 1 0Z" fill="#ddd"/></svg><span>+44 0161 555 0142</span></div>
    <div class="contact-row"><svg width="10" height="8" viewBox="0 0 10 8"><rect width="10" height="8" fill="#ddd"/><path d="M0 0 L5 4.5 L10 0" stroke="#2b2b2b" fill="none"/></svg><span>studio@stonereach.example</span></div>
  </div>
  <div class="footer-col col-news">
    <h3><strong>NEWSLETTER</strong> SIGNUP</h3>
    <p>Sign up with us to get updates on our latest homes</p>
    <div class="field">Your Name</div>
    <div class="field">Your Email</div>
    <span class="subscribe">Subscribe</span>
  </div>
  <div class="footer-col col-social">
    <h3><strong>SOCIAL</strong> CONNECT</h3>
    <div class="social-row"><span class="social-dot"></span>JOURNAL</div>
    <div class="social-row"><span class="social-dot"></span>PORTFOLIO</div>
    <div class="social-row"><span class="social-dot"></span>UPDATES</div>
  </div>
</footer>

<div class="legal-bar">
  <span>Copyright 2015 Stonereach Architect. All Rights Reserved</span>
  <span>Terms and Conditions &nbsp;|&nbsp; Privacy Policy</span>
</div>

</body>
</html>
```